A clean crisp business card for a Landscape Construction company. Designed to be easy to read contact/ info and also be appealing/interesting, unlike a traditional business card.

Industry/Entity Type

Landscape Construction

Contact Information for Business Card

Company name : Brambleford Landscape Construction, phone number: (877) 62Vista, website:Bramblefordyards.example, Email, sales@bramblefordyards.example

Requirements
Nice to have
• Luxurious finishes/ details…. Icons or emblems next to contact info
Should not have
• Clipart or general pictures

```html
<!DOCTYPE html>
<html lang="en">
<head>
<meta charset="utf-8">
<title>Brambleford Landscape Construction – Business Card</title>
<link rel="stylesheet" href="https://fonts.googleapis.com/css2?family=Cinzel:wght@600&family=Open+Sans:wght@400;600&display=swap">
<style>
  :root {
    --backdrop: #2a2a2a;
    --card-dark: #232323;
    --card-blue: #2f73c0;
    --blue-deep: #2563ad;
    --brand-blue: #2b72c6;
    --brand-green: #8cc63f;
    --ink-light: #f2f2f2;
  }
  * { margin: 0; padding: 0; box-sizing: border-box; }
  html, body { width: 1200px; height: 900px; overflow: hidden; }
  body {
    background: var(--backdrop);
    font-family: "Open Sans", sans-serif;
    position: relative;
  }
  .card {
    position: absolute;
    left: 250px;
    width: 700px;
    height: 400px;
    border-radius: 2px;
    box-shadow: 0 10px 30px rgba(0,0,0,.45);
  }
  .card-front {
    top: 35px;
    background: linear-gradient(135deg, #2a69b8 0%, var(--card-blue) 60%, #3a7fc8 100%);
    display: flex;
    align-items: center;
    justify-content: center;
  }
  .front-wordmark {
    font-family: "Cinzel", serif;
    font-weight: 600;
    color: var(--blue-deep);
    font-size: 40px;
    letter-spacing: 2px;
    text-align: center;
    line-height: 1.25;
  }
  .front-wordmark .sub { display: block; font-size: 19px; letter-spacing: 6px; }
  .card-back {
    top: 465px;
    background: var(--card-dark);
    display: flex;
    align-items: center;
    padding: 0 40px 0 44px;
  }
  .back-wordmark {
    width: 300px;
    font-family: "Cinzel", serif;
    font-weight: 600;
    color: var(--brand-green);
    font-size: 30px;
    line-height: 1.25;
    letter-spacing: 1px;
  }
  .back-wordmark .sub { display: block; font-size: 14px; letter-spacing: 3.5px; }
  .divider {
    width: 6px;
    height: 220px;
    margin: 0 26px 0 14px;
    display: flex;
    flex-direction: column;
    align-items: center;
  }
  .divider .thin { width: 2px; flex: 1; background: var(--brand-green); }
  .divider .thick { width: 6px; flex: 3; background: var(--brand-blue); margin: 8px 0; }
  .contact { color: var(--ink-light); font-size: 15px; line-height: 1.55; }
  .person-name {
    font-family: "Cinzel", serif;
    font-weight: 600;
    font-size: 26px;
    letter-spacing: 2px;
    line-height: 1.1;
  }
  .person-name .first { color: var(--brand-blue); }
  .person-name .last { color: var(--brand-green); }
  .person-role { font-size: 15px; margin-bottom: 12px; }
  .address { margin-bottom: 8px; }
  .contact-line { display: flex; align-items: center; gap: 10px; }
  .contact-line svg { width: 18px; height: 18px; flex: none; fill: var(--brand-green); }
</style>
</head>
<body>
  <section class="card card-front">
    <div class="front-wordmark">Brambleford<span class="sub">Landscape Construction</span></div>
  </section>

  <section class="card card-back">
    <div class="back-wordmark">Brambleford<span class="sub">Landscape Construction</span></div>
    <div class="divider"><span class="thin"></span><span class="thick"></span><span class="thin"></span></div>
    <div class="contact">
      <div class="person-name"><span class="first">Dale</span> <span class="last">Fenwick</span></div>
      <div class="person-role">Director</div>
      <div class="address">4410 Harrow Mill Rd.,<br>Suite 118, Ashgrove, OH 45990</div>
      <div class="contact-line">
        <svg viewBox="0 0 24 24" aria-hidden="true"><path d="M6.6 10.8a15.2 15.2 0 0 0 6.6 6.6l2.2-2.2c.3-.3.7-.4 1-.2 1.1.4 2.3.6 3.6.6.6 0 1 .4 1 1V20c0 .6-.4 1-1 1A17 17 0 0 1 3 4c0-.6.4-1 1-1h3.5c.6 0 1 .4 1 1 0 1.3.2 2.5.6 3.6.1.3 0 .7-.2 1z"/></svg>
        <span>(877) 62Vista</span>
      </div>
      <div class="contact-line">
        <svg viewBox="0 0 24 24" aria-hidden="true"><path d="M2 5h20v14H2z M2 5l10 8 10-8" stroke="#232323" stroke-width="1.6"/></svg>
        <span>sales@bramblefordyards.example</span>
      </div>
      <div class="contact-line">
        <svg viewBox="0 0 24 24" aria-hidden="true"><circle cx="12" cy="12" r="10"/><path d="M2 12h20M12 2c3 3 3 17 0 20M12 2c-3 3-3 17 0 20" stroke="#232323" stroke-width="1.4" fill="none"/></svg>
        <span>www.bramblefordyards.example</span>
      </div>
    </div>
  </section>
</body>
</html>
```